REdesign Landing Page für Reise- und Touristikportal
Zielgruppe
Nachtrag 25.10.21: es bedarf keines neuen Logos. Aber die Angebotsboxen auf der Startseite, die auch in den Reiserubriken vorzufinden sind, dürfen gern optisch angepasst werden. Die jeweilige Balkenfarbe ist stets die Farbe des Reiseveranstalters und das Logo des Veranstalters in der Box sollte weiterhin vorhanden sein (dienen zur Wiedererkennung).
Reise- und Touristikportal https://wegfinderei.de, mit zahlreichen Reiseangeboten namhafter (Spezial-) Reiseveranstalter. Es handelt sich um ein Affiliate Portal, d.h. die Reisen werden stets auf der Seite der Reiseveranstalter gebucht. Zielgruppe, sind die Personen, die Wert auf schöne Reisen legen (kein Mainstream wie VAK), die ihre Reisen auch z.b. nach ihrem Hobby aussuchen wollen (z.B. Motorradreisen, Tauchreisen etc.) oder auch besondere Filterfunktionen zum Finden der Reise nutzen möchten.
Aufgabenstellung
- Redesign Startseite mit 'Hier will ich bleiben' Effekt (nicht nur Farbänderung oder Elemente anders platzieren)
- wirkungsvolles responsive Design soll unsere Zielgruppe neugierig machen, ansprechen und zum Anklicken der Angebote, Verweilen einladen
- angenehmes Farbschemata (above/under the fold)
- ansprechende Aufteilung der Startseiten Bereiche (aktuell wirkt das alles wie ein 'Schlauch')
- mobil leicht zu bedienen (das ist aktuell ein großes Problem, wegen der 53 Reisethemen Kacheln)
- wir möchten mit der neuen Startseite das Bedürfnis nach Urlaub wecken und auf Reiseveranstalter Seite das Gefühl wecken 'Hier müssen wir unbedingt unsere Angebote einstellen'
- ein schöner Footer (der jetzige ist fürchterlich)
- schlanke Performance (IT Umsetzung erfolgt dann durch einen Programmierer)
- die engl. Seite fällt künftig weg, also Entwurf ohne den 'de' Umschalter
Ich bin nicht an das jetzige Design, Schriften der Startseite, Anordnung der einzelnen Bereiche gebunden. Allerdings wird an den Reiserubrikseiten designmäßig nichts bis wenig geändert werden (außer es ginge schnell) und die Startseite soll natürlich weiterhin zum Rest der Webseite passen. Aktuell verwendete Schriftart: Lato.
Man kann auch z.B. Neues integrieren wie z.B. 'Was für ein Reisetyp bist Du?' oder 'Was ist Deine Lieblingsreisezeit?' als eine Art Quiz (technisch würde das von einem Programmierer umgesetzt werden)
Ich kann auch Zugang zu Lumora Bildarchiv geben. Man könnte z.b. (ist kein Muss und sofern passend) die im Footer genannte Partnerseite auflösen und evtl. in grau eine Auswahl im unteren Bereich der Startseite nennen.
Was ist Ihr erster Eindruck von der Startseite https://wegfinderei.de ? Was gefällt Ihnen nicht und würden Sie ändern wollen?

```html
<!DOCTYPE html>
<html lang="de">
<head>
<meta charset="utf-8">
<title>Wegfinderei – Reiseangebote</title>
<link href="https://fonts.googleapis.com/css2?family=Roboto:wght@400;500;700&family=Roboto+Slab:wght@300;400&display=swap" rel="stylesheet">
<style>
:root{
  --gold:#c9a024;
  --navy:#1c2150;
  --ink:#2f2f2f;
  --soft:#ececec;
  --quiz-bg:#efefef;
  --quiz-blue:#2e3d7c;
  --green:#5f8a62;
  --blue:#4d5f95;
  --red:#a64a45;
  --white:#fff;
  --serif:'Roboto Slab',serif;
  --sans:'Roboto',sans-serif;
}
*{box-sizing:border-box;margin:0;padding:0}
html,body{width:1200px;height:4296px;overflow:hidden}
body{font-family:var(--sans);color:var(--ink);background:var(--white);position:relative}
a{color:inherit;text-decoration:none}

/* Hero */
.hero{position:absolute;left:0;top:0;width:1200px;height:633px;
  background:linear-gradient(180deg,#5b6a6a 0%,#8f8a73 30%,#6d7a52 55%,#3e4d2c 80%,#2f3a22 100%);}
.hero-glow{position:absolute;right:80px;top:180px;width:380px;height:200px;border-radius:50%;
  background:radial-gradient(closest-side,rgba(255,214,140,.55),rgba(255,214,140,0));}
.brand{position:absolute;left:0;right:0;top:24px;text-align:center;font-weight:500;font-size:18px;color:var(--gold);letter-spacing:.5px}
.brand small{display:block;font-size:9px;font-weight:500;margin-top:2px;letter-spacing:.3px}
.main-nav{position:absolute;left:0;right:0;top:76px;display:flex;justify-content:center;gap:24px;font-size:12.5px;font-weight:700;color:#fff}
.main-nav .active{color:var(--gold)}
.hero h1{position:absolute;left:0;right:0;top:298px;text-align:center;font-family:var(--serif);font-weight:400;color:var(--gold);font-size:27px;line-height:38px}
.hero p{position:absolute;left:300px;width:600px;top:378px;text-align:center;color:#fff;font-size:16px;line-height:29px;font-weight:500}

/* Search */
.search-tabs{position:absolute;left:0;right:0;top:680px;display:flex;justify-content:center;gap:26px;font-size:13px;font-weight:500;color:#444}
.search-tabs .active{color:var(--gold);border-bottom:2px solid var(--gold);padding-bottom:3px}
.search-fields{position:absolute;top:724px;left:130px;display:flex;gap:16px}
.field{height:50px;border-radius:25px;background:#fff;box-shadow:0 3px 12px rgba(0,0,0,.13);font-size:16px;color:#666;display:flex;align-items:center;justify-content:center}
.go{position:absolute;left:521px;top:797px;width:192px;height:41px;border-radius:21px;background:var(--gold);color:#fff;font-size:12px;font-weight:700;display:flex;align-items:center;justify-content:center;letter-spacing:.5px}

/* Categories */
.cat-card{position:absolute;left:38px;top:918px;width:276px;height:560px;background:#fff;border-radius:10px;box-shadow:0 4px 22px rgba(0,0,0,.12);padding:34px 23px}
.cat-card h3{font-size:13.5px;font-weight:700;color:var(--navy);margin-bottom:10px}
.cat-card li{list-style:none;font-size:10.8px;color:var(--quiz-blue);line-height:22.5px}
.pill{display:inline-block;margin-top:18px;padding:6px 10px;border-radius:12px;box-shadow:0 2px 7px rgba(0,0,0,.15);font-size:8.5px;font-weight:700;color:#333}
.tile{position:absolute;display:flex;align-items:flex-end;padding:18px 20px;color:#fff;font-family:var(--serif);font-size:19px;line-height:24px}
.dots{position:absolute;display:flex;gap:6px}
.dot{width:12px;height:12px;border-radius:50%;background:#cfcfcf}
.dot.on{width:17px;height:17px;background:var(--gold);margin-top:-2px}

/* Offers */
.offers{position:absolute;left:0;top:1605px;width:1200px;height:717px;background:var(--soft)}
.sec-title{position:absolute;left:0;right:0;text-align:center;font-family:var(--serif);font-weight:400;font-size:30px;color:#2b2b2b}
.offer-tabs{position:absolute;left:0;right:0;top:100px;display:flex;justify-content:center;gap:26px;font-size:13.5px;font-weight:500;color:var(--quiz-blue)}
.offer-tabs .active{color:var(--gold);border-bottom:2px solid var(--gold);padding-bottom:4px}
.offer{position:absolute;top:150px;width:257px;height:457px;background:#fff;border-radius:6px;box-shadow:0 2px 10px rgba(0,0,0,.1);overflow:hidden}
.offer .pic{height:148px}
.offer .bar{height:5px}
.offer .body{padding:12px 18px}
.offer h4{font-family:var(--serif);font-weight:400;font-size:17.5px;line-height:23px;height:50px}
.offer ul{margin:6px 0 0 12px;font-size:10.5px;line-height:15.5px;color:#555}
.offer .price{font-size:20px;font-weight:700;margin-top:12px;color:#2b2b2b}
.offer .note{font-size:10.5px;color:#555;margin-top:3px}
.offer .cta{margin-top:9px;height:39px;border-radius:20px;color:#fff;font-size:12.5px;font-weight:700;display:flex;align-items:center;justify-content:center;letter-spacing:.5px}
.offer .more{margin:10px auto 0;width:80px;height:20px;border-radius:10px;box-shadow:0 1px 5px rgba(0,0,0,.15);font-size:8px;font-weight:700;display:flex;align-items:center;justify-content:center}

/* Magazine */
.mag{position:absolute;display:flex;flex-direction:column;justify-content:flex-end;padding:30px 30px;color:#fff}
.mag h4{font-family:var(--serif);font-weight:400;font-size:25px;line-height:32px;margin-bottom:14px}
.mag .read{width:118px;height:28px;border-radius:14px;background:#fff;color:#222;font-size:9px;font-weight:700;display:flex;align-items:center;justify-content:center}

/* Quiz */
.quiz{position:absolute;left:0;top:3178px;width:1200px;height:622px;background:var(--quiz-bg)}
.quiz-card{position:absolute;left:213px;top:157px;width:774px;height:333px;background:#fff;border-radius:22px;box-shadow:0 3px 14px rgba(0,0,0,.1)}
.quiz-card h4{position:absolute;left:0;right:0;top:32px;text-align:center;font-size:20px;font-weight:500;color:var(--quiz-blue)}
.choice{position:absolute;top:77px;width:207px}
.choice .pic{height:156px}
.choice p{text-align:center;font-size:13px;font-weight:500;color:var(--quiz-blue);margin-top:13px}
.step{position:absolute;left:0;right:0;top:300px;text-align:center;font-size:19px;font-weight:500;color:#999}

/* Footer */
.footer{position:absolute;left:0;top:3800px;width:1200px;height:496px;background:var(--navy);color:#fff}
.footer h5{position:absolute;font-size:15px;font-weight:700;color:var(--gold)}
.fcol{position:absolute;font-size:16px;line-height:29px}
.fbrand{position:absolute;left:787px;top:58px;font-size:34px;font-weight:500;color:var(--gold);letter-spacing:.5px}
.ftag{position:absolute;left:790px;top:103px;font-size:17px;font-weight:500;color:var(--gold)}
.flegal{position:absolute;left:790px;width:360px;font-size:12.5px;line-height:22.5px;color:#e6e6ee}
.social{position:absolute;left:790px;top:413px;display:flex;gap:24px}
.social span{width:24px;height:24px;border:2px solid #aab;border-radius:50%}
.copy{position:absolute;left:57px;top:425px;font-size:11px;color:#ccd}
</style>
</head>
<body>

<header class="hero">
  <div class="hero-glow"></div>
  <div role="img" aria-label="Nebelige grüne Berglandschaft im Sonnenuntergang" style="position:absolute;inset:0"></div>
  <div class="brand">WEGFINDEREI<small>Unterwegs mit offenen Augen</small></div>
  <nav class="main-nav">
    <a class="active">Reiseangebote</a><a>Aktivitäten&amp;Touren</a><a>Hotels</a><a>Flüge</a><a>Konzerte&amp;Events</a><a>Reisemagazin</a><a>Dein Freebie</a><a>Kurzurlaube&amp;Hotelarrangements</a>
  </nav>
  <h1>STELL DIR VOR, DU BUCHST GERADE DEINEN NÄCHSTEN<br>URLAUB – und kannst es kaum erwarten, bis es los geht!</h1>
  <p>Hol Dir jetzt diesen Moment mit Reiseangeboten für 2022, die auch Dich begeistern: als Familie, Single, Kurzurlauber, Genießer, Sportler oder Kulturliebhaber.</p>
</header>

<section class="search">
  <div class="search-tabs"><span class="active">Reiseangebote</span><span>Aktivitäten &amp; Touren</span><span>Hotels</span><span>Flüge</span><span>Konzerte &amp; Events</span></div>
  <div class="search-fields">
    <div class="field" style="width:250px">Wähle eine Reiserubrik</div>
    <div class="field" style="width:250px">Wähle dein Reiseland</div>
    <div class="field" style="width:163px">Stadt</div>
    <div class="field" style="width:225px">Stichwortsuche</div>
  </div>
  <a class="go">LEG LOS!</a>
</section>

<section class="categories">
  <aside class="cat-card">
    <h3>Kategorien:</h3>
    <ul>
      <li>Autoreisen und Autorundreisen (76)</li><li>Badeurlaub &amp; Strandurlaub (111)</li><li>Bahnreisen (82)</li><li>Best of Reisen (42)</li><li>Busreisen (60)</li><li>Camping und Mobilehomes (137)</li><li>Cluburlaub (40)</li><li>Erlebnisreisen (960)</li><li>Expeditionen (12)</li><li>Fahrradreisen (111)</li><li>Familienreisen (84)</li><li>Ferienhäuser und Ferienwohn. (12707)</li><li>Flußkreutzfahrten (493)</li><li>Frauenreisen</li><li>Freizeitparks und Zoos (62)</li><li>Golfreisen (3)</li><li>Gourmetreisen (38)</li><li>Hausbootreisen (25)</li><li>Kinder- und Jugenreisen</li>
    </ul>
    <span class="pill">MEHR RUBRIKEN</span>
  </aside>
  <a class="tile" role="img" aria-label="Kurvige Straße durch Herbstwald" style="left:333px;top:900px;width:442px;height:308px;background:linear-gradient(160deg,#c9652a,#8a3a1c 60%,#4b3a33)"><span>Autorundreisen und<br>Autoreisen (76)</span></a>
  <a class="tile" role="img" aria-label="Hängematte am türkisen Strand" style="left:333px;top:1213px;width:442px;height:285px;background:linear-gradient(160deg,#6fc4d0,#2e8fa8 55%,#2b5466)"><span>Badeurlaub &amp;<br>Strandurlaub (111)</span></a>
  <a class="tile" role="img" aria-label="Paar im Zugabteil" style="left:780px;top:900px;width:363px;height:242px;background:linear-gradient(160deg,#c9cfc8,#8a9488 60%,#4f5750)"><span>Bahnreisen (82)</span></a>
  <a class="tile" role="img" aria-label="Wohnmobil im Wald" style="left:780px;top:1147px;width:363px;height:173px;background:linear-gradient(160deg,#a0876a,#5c4c38 60%,#3a3426)"><span>Camping und Mobilehomes (137)</span></a>
  <a class="tile" role="img" aria-label="Wanderin im grünen Dschungel" style="left:780px;top:1325px;width:363px;height:173px;background:linear-gradient(160deg,#8fa77a,#4f6b3d 60%,#344a28)"><span>Erlebnisreisen (960)</span></a>
  <div class="dots" style="left:717px;top:1527px"><i class="dot on"></i><i class="dot"></i><i class="dot"></i><i class="dot"></i><i class="dot"></i><i class="dot"></i></div>
</section>

<section class="offers">
  <h2 class="sec-title" style="top:40px">Unsere Top-Angebote für Sie</h2>
  <div class="offer-tabs"><span class="active">Wellness im Herbst</span><span>Kurzurlaube &amp; Hotelarrangements</span><span>Reiseangebote des Monats</span></div>

  <article class="offer" style="left:57px">
    <div class="pic" role="img" aria-label="Ostseestrand mit Hotel an der Küste" style="background:linear-gradient(180deg,#6fb1e0,#2c7bb6 50%,#d9c9a5)"></div>
    <div class="bar" style="background:var(--green)"></div>
    <div class="body">
      <h4 style="color:var(--green)">Wellnesshotel mit Goldbad und Massage - Ostsee</h4>
      <ul><li>5 Übernachtungen im Standard-DZ</li><li>Begrüßungsdrink</li><li>Reichhaltiges Frühstücksbuffet</li><li>Abends vielseitiges kalt-warmes Bu...</li><li>Klassische Teilmassage (20min.)</li></ul>
      <div class="price">ab € 229,00</div><div class="note">5 Übernachtungen inkl.Halbpension *</div>
      <div class="cta" style="background:var(--green)">WEITER ZUM ANGEBOT</div><div class="more">MEHR DETAILS</div>
    </div>
  </article>
  <article class="offer" style="left:333px">
    <div class="pic" role="img" aria-label="Dünengras vor blauem Himmel" style="background:linear-gradient(180deg,#a9cbe0,#8fae8a 55%,#d6cfb5)"></div>
    <div class="bar" style="background:var(--blue)"></div>
    <div class="body">
      <h4 style="color:var(--blue)">Wellness-Auszeit mit Meerblick - Kolberg</h4>
      <ul><li>5 Übernachtungen im Standard-DZ</li><li>Begrüßungsdrink</li><li>Reichhaltiges Frühstücksbuffet</li><li>Abends vielseitiges kalt-warmes Bu...</li><li>Entspannte Teilkörpermassage</li></ul>
      <div class="price">ab € 169,00</div><div class="note">3 Übernachtungen inkl. Frühstück *</div>
      <div class="cta" style="background:var(--blue)">WEITER ZUM ANGEBOT</div><div class="more">MEHR DETAILS</div>
    </div>
  </article>
  <article class="offer" style="left:610px">
    <div class="pic" role="img" aria-label="Kurpark mit Wegen und Kolonnade" style="background:linear-gradient(180deg,#5f8e3a,#8fb05a 50%,#b49a68)"></div>
    <div class="bar" style="background:var(--red)"></div>
    <div class="body">
      <h4 style="color:var(--red)">Kompforthotel mit Spa-Bereich-Marienbad</h4>
      <ul><li>5 Übernachtungen im Standard-DZ</li><li>Begrüßungsdrink</li><li>Reichhaltiges Frühstücksbuffet</li><li>Abends vielseitiges kalt-warmes Bu...</li><li>Klassische Teilmassage (20min.)</li></ul>
      <div class="price">ab € 299,00</div><div class="note">5 Übernachtungen inkl. Halbpension *</div>
      <div class="cta" style="background:var(--red)">WEITER ZUM ANGEBOT</div><div class="more">MEHR DETAILS</div>
    </div>
  </article>
  <article class="offer" style="left:887px">
    <div class="pic" role="img" aria-label="Wellnessliege mit Obstschale" style="background:linear-gradient(180deg,#6b4a2c,#a8773f 50%,#d9b88a)"></div>
    <div class="bar" style="background:var(--red)"></div>
    <div class="body">
      <h4 style="color:var(--red)">Wellnessreise in die Seenstadt Schwerin</h4>
      <ul><li>5 Übernachtungen im Standard-DZ</li><li>Begrüßungsdrink</li><li>Reichhaltiges Frühstücksbuffet</li><li>Abends vielseitiges kalt-warmes Bu...</li><li>Klassische Teilmassage (20min.)</li></ul>
      <div class="price">ab € 149,00</div><div class="note">2 Übernachtungen inkl. Frühstück *</div>
      <div class="cta" style="background:var(--red)">WEITER ZUM ANGEBOT</div><div class="more">MEHR DETAILS</div>
    </div>
  </article>
  <div class="dots" style="left:541px;top:640px"><i class="dot on"></i><i class="dot"></i><i class="dot"></i><i class="dot"></i><i class="dot"></i><i class="dot"></i></div>
</section>

<section class="magazine">
  <h2 class="sec-title" style="top:2380px">Unser Reisemagazin</h2>
  <a class="mag" role="img" aria-label="Kubanisches Porträt mit blauem Kopftuch und Zigarre" style="left:57px;top:2445px;width:533px;height:658px;background:linear-gradient(150deg,#2d4fb0,#3b3e6a 45%,#4a3024 80%,#2e1d16)">
    <h4>Kuba - Kolonialromantik<br>und ein Hauch von<br>Revolution</h4><span class="read">ARTIKEL LESEN</span>
  </a>
  <a class="mag" role="img" aria-label="Backsteinspeicher an einem Kanal in Hamburg" style="left:595px;top:2445px;width:548px;height:327px;background:linear-gradient(170deg,#c3ccd3,#8a4a38 45%,#4e3028)">
    <h4>Hamburg - Eine Reise mit<br>Fernwehgarantie</h4><span class="read">ARTIKEL LESEN</span>
  </a>
  <a class="mag" role="img" aria-label="Weiße Kathedrale am Hafen von Helsinki" style="left:595px;top:2777px;width:548px;height:326px;background:linear-gradient(180deg,#9fc2dc,#d8dde0 45%,#5a6f80 70%,#2f3b46)">
    <h4>Helsinki - Die weiße<br>Stadt am Meer</h4><span class="read">ARTIKEL LESEN</span>
  </a>
</section>

<section class="quiz">
  <h2 class="sec-title" style="top:100px">Was für ein Reisetyp bist Du?</h2>
  <div class="quiz-card">
    <h4>Was klingt für dich nach einem rundum tollen Wochenende?</h4>
    <div class="choice" style="left:64px"><div class="pic" role="img" aria-label="Yoga am Strand bei Sonnenaufgang" style="background:linear-gradient(180deg,#c9d3d8,#8fa3ad 55%,#5c6b72)"></div><p>Yoga am Strand</p></div>
    <div class="choice" style="left:289px"><div class="pic" role="img" aria-label="Wanderer auf einem Bergpfad" style="background:linear-gradient(180deg,#9fb0b8,#4d5a4f 55%,#2f3832)"></div><p>Auf unbekannten Pfade gehen</p></div>
    <div class="choice" style="left:515px"><div class="pic" role="img" aria-label="Kochkurs in einer Profiküche" style="background:linear-gradient(180deg,#d8d4cc,#9a938a 55%,#5a554f)"></div><p>Neues lernen</p></div>
    <div class="step">Schritt 1 von 4</div>
  </div>
</section>

<footer class="footer">
  <h5 style="left:57px;top:66px">Rubriken</h5>
  <div class="fcol" style="left:57px;top:88px">Reiseangebote<br>Aktivitäten &amp; Touren<br>Flüge</div>
  <div class="fcol" style="left:255px;top:88px">Konzerte&amp;Events<br>Reisemagazin<br>Dein Freebie</div>
  <div class="fcol" style="left:472px;top:88px;line-height:25px">Kurzurlaube &amp;<br>Hotelarrangements</div>
  <h5 style="left:57px;top:235px">Service</h5>
  <div class="fcol" style="left:57px;top:257px">Kontakt<br>Partnerprogramm<br>Partner<br>Social Media</div>
  <div class="fcol" style="left:255px;top:257px">Impressum<br>Datenschutzerklärung<br>Nutzungsbedingungen<br>FAQs</div>
  <div class="fcol" style="left:472px;top:257px">Reisezitate<br>Visum beantragen</div>
  <div class="fbrand">WEGFINDEREI</div>
  <div class="ftag">Unterwegs mit offenen Augen</div>
  <p class="flegal" style="top:147px">Bei der auf dieser Seite dargestellten Reise- und Ticket­angebote, handelt es sich um Angebote von dritten Unter­nehmen, auf die WEGFINDEREI keinen Einfluss hat.</p>
  <p class="flegal" style="top:232px">Die mit Sternchen (*) gekennzeichneten Links sind Provisions-Links, auch Affiliate-Links genannt. Wenn Sie auf einen solchen Link klicken und auf der Zielseite etwas kaufen, bekommen wir vom betreffenden Anbieter eine Vermittlerprovision. Es entstehen für Sie keine Nachteile beim Kauf oder Preis.</p>
  <div class="social" aria-label="Soziale Netzwerke"><span></span><span></span><span></span><span></span></div>
  <div class="copy">© Copyright 2021 wegfinderei.de</div>
</footer>

</body>
</html>
```